Web Design Project

Psychotherapy and Counselling Practice needs a landing page web design.

My business "Larkfield Advisory" specialises in the treatment of Anxiety and Depression with a holistic approach, endeavouring to unlock the key that holds us to ransom in a life that is imbalanced, frustrating, and ultimately of our own making due to our own perceptions and behaviours.

There is much that impacts us which we cannot change, but we are always in control of how we think, and how we frame our experiences.....learning to challenge those thoughts and behaviours that are destructive and disempowering opens up a world of joyful possibility. Life is about making choices, learn to make wiser and healthier choices.......

Larkfield Advisory has a client base of individual clients but will seek to expand to offer services to the Corporate world by offering an adjunct to employers for established "Wellness Programs".

Larkfield Advisory is a highly professional, ethically bound business, with the needs of the client at the forefront of all we do.

Larkfield Advisory wishes to avoid the usual "jargon driven" psychobabble offered on many counselling web pages. It aims to be stylishly presented, clean in look and with as few "words" as possible and a largely white background (faster loading and more powerful impact of what is stated), those words contained in the webpage should be meaningful, persuasive and have an impact simply at glance. Larkfield does not want , or expect, those prospective clients in need of support , to be reading through volumes of industry driven cliches.

At this point Larkfield is just looking for a high quality landing page. However in time this will likely expand to include other sections such as case studies, video content etc.

Target Market(s)

Those in need of emotional support, suffering mental health issues, and those simply wanting to become self aware supported by a mindful therapist.

Industry/Entity Type

Industry

Requirements
Must have
• The design must incorporate the Larkfield logo and colour schemes found on the attached files.

```html
<!DOCTYPE html>
<html lang="en">
<head>
<meta charset="utf-8">
<title>Larkfield Advisory</title>
<link href="https://fonts.googleapis.com/css2?family=Andika:wght@400;700&display=swap" rel="stylesheet">
<style>
  :root {
    --slate: #323e48;
    --green: #7ba100;
    --leaf: #8cb31a;
    --grey: #6e6e6e;
    --mid-grey: #8a8a8a;
    --light: #b9c0c6;
    --white: #ffffff;
    --ink: #3b3b3b;
    --photo-a: #c9b9a3;
    --photo-b: #9aa7b5;
  }
  * { margin: 0; padding: 0; box-sizing: border-box; }
  html, body { width: 1200px; height: 1000px; overflow: hidden; background: var(--white); }
  body { font-family: "Andika", sans-serif; position: relative; letter-spacing: 1.5px; }
  .page { position: absolute; left: 119px; top: 19px; width: 966px; height: 966px; }

  .header { position: absolute; left: 0; top: 0; width: 966px; height: 153px; background: var(--slate); }
  .nav { position: absolute; left: 0; top: 106px; width: 487px; height: 47px; background: var(--green);
         display: flex; align-items: center; padding-left: 30px; gap: 0; }
  .nav a { color: var(--white); text-decoration: none; font-size: 14px; font-weight: 700; letter-spacing: 2px; }
  .nav a:nth-child(1) { width: 88px; }
  .nav a:nth-child(2) { width: 116px; }
  .nav a:nth-child(3) { width: 109px; }

  .brand-tile { position: absolute; left: 548px; top: 26px; width: 108px; height: 107px; background: var(--grey);
                border-radius: 3px; display: flex; align-items: center; justify-content: center;
                color: var(--leaf); font-size: 17px; letter-spacing: 0.5px; }
  .practitioner { position: absolute; left: 666px; top: 22px; color: var(--light); }
  .practitioner .name { font-size: 19px; letter-spacing: 3px; }
  .practitioner .quals { font-size: 14px; letter-spacing: 2px; margin-top: 6px; }
  .practitioner .contact { font-size: 14px; letter-spacing: 2px; margin-top: 28px; line-height: 21px; }

  .hero { position: absolute; left: 0; top: 153px; width: 966px; height: 583px; background: var(--white);
          border-left: 1px solid var(--mid-grey); border-right: 1px solid var(--mid-grey); overflow: hidden; }
  .hero-mark { position: absolute; left: 64px; top: 270px; display: flex; align-items: center; gap: 18px; }
  .hero-mark .dot { width: 22px; height: 22px; background: var(--leaf); }
  .hero-mark span { font-size: 66px; color: var(--leaf); letter-spacing: 2px; line-height: 1; }
  .swoosh { position: absolute; left: 0; top: 470px; }

  .welcome { position: absolute; left: 490px; top: 18px; width: 475px; }
  .welcome h1 { text-align: center; color: var(--green); font-size: 15px; font-weight: 700; letter-spacing: 2px; }
  .welcome p { margin: 17px 22px 0 20px; font-size: 10.5px; line-height: 12.5px; color: var(--ink); letter-spacing: 1.4px; }
  .photo { position: absolute; left: 507px; top: 167px; width: 449px; height: 298px;
           background: linear-gradient(135deg, var(--photo-a), #e2d6c4 45%, var(--photo-b)); }

  .tagline { position: absolute; left: 0; top: 736px; width: 487px; height: 125px; background: var(--white); }
  .tagline p { position: absolute; left: 20px; top: 52px; font-size: 14px; color: var(--grey); letter-spacing: 2px; }
  .tagline b { color: var(--green); font-weight: 400; }

  .social { position: absolute; left: 0; top: 861px; width: 487px; height: 49px; background: var(--slate); }
  .social .tile { position: absolute; top: 9px; width: 32px; height: 32px; background: var(--white); border-radius: 6px; }
  .social .url { position: absolute; left: 118px; top: 15px; font-size: 14px; color: var(--grey); letter-spacing: 2px; }
  .social .url b { color: var(--green); font-weight: 400; }

  .news { position: absolute; left: 487px; top: 736px; width: 479px; height: 174px; background: var(--slate); }
  .news h2 { text-align: center; color: var(--green); font-size: 14px; font-weight: 700; letter-spacing: 2px; margin-top: 14px; }
  .news .card { position: absolute; left: 61px; top: 34px; width: 365px; height: 140px; background: var(--white);
                border-radius: 6px; padding: 24px 10px 0 12px; }
  .news .card p { font-size: 8.6px; line-height: 13px; color: var(--ink); letter-spacing: 1px; }

  .footer { position: absolute; left: 0; top: 910px; width: 966px; height: 56px; background: var(--green); }
  .footer p { position: absolute; left: 29px; top: 21px; font-size: 8px; font-weight: 700; color: var(--white); letter-spacing: 1px; }
</style>
</head>
<body>
<div class="page">
  <header class="header">
    <nav class="nav">
      <a href="#">Home</a>
      <a href="#">About Us</a>
      <a href="#">Contact</a>
      <a href="#">Our services</a>
    </nav>
    <div class="brand-tile">Larkfield</div>
    <div class="practitioner">
      <div class="name">MARA QUILL</div>
      <div class="quals">BA (Psych) BSc (Hons) Psych MBPS</div>
      <div class="contact">Mobile: 0400 218 765<br>E-mail: mara.quill@larkmail.net</div>
    </div>
  </header>

  <section class="hero">
    <div class="hero-mark"><div class="dot"></div><span>Larkfield</span></div>
    <svg class="swoosh" width="966" height="113" viewBox="0 0 966 113" aria-hidden="true">
      <path d="M0 70 Q200 20 860 26 Q930 27 866 32 Q300 40 0 80 Z" fill="#8cb31a"/>
      <path d="M0 82 Q330 34 966 40 L966 113 L0 113 Z" fill="#6e6e6e"/>
      <path d="M0 86 Q330 40 966 46" stroke="#9a9a9a" stroke-width="2" fill="none"/>
    </svg>
    <div class="welcome">
      <h1>Welcome to Larkfield</h1>
      <p>"Lorem ipsum dolor sit amet, consectetur adipisicing elit,sed do eiusmod tempor incididunt ut labore et dolore magna aliqua. Ut enim ad minim veniam,quis nostrud exercitation ullamco laboris nisi ut aliquip ex ea commodo consequat.Duis aute irure dolor in reprehenderit in voluptate velit esse cillum dolore eu fugiat nulla pariatur. Excepteur sint occaecat cupidatat non proident,sunt in culpa qui officia deserunt mollit anim id est laborum."</p>
    </div>
    <div class="photo" role="img" aria-label="Photo of a counselling session in a bright sitting room"></div>
  </section>

  <section class="tagline">
    <p><b>Larkfield Advisory</b> is highly Professional</p>
  </section>

  <section class="social">
    <div class="tile" style="left:19px"></div>
    <div class="tile" style="left:60px"></div>
    <div class="url">www.<b>larkfieldadvisory</b>.com.au</div>
  </section>

  <section class="news">
    <h2>What's News</h2>
    <div class="card">
      <p>"Lorem ipsum dolor sit amet, consectetur adipisicing elit,sed do eiusmod tempor incididunt ut labore et dolore magna aliqua. Ut enim ad minim veniam,quis nostrud exercitation ullamco laboris nisi ut aliquip ex ea commodo consequat. Duis aute irure dolor in reprehenderit in voluptate velit esse cillum dolore eu fugiat nulla pariatur. Excepteur sint occaecat cupidatat non proident, sunt in culpa qui officia deserunt mollit anim id est laborum."</p>
    </div>
  </section>

  <footer class="footer">
    <p>Copyright Larkfield 2013</p>
  </footer>
</div>
</body>
</html>
```